Design new marketing postcard for mortgage loan applicants

I have provided a postcard recently designed as a possible guide for this project and have attached it. The new text is rough drafted and included. Please feel free to design outside of the old postcard or you can design close to it.

```html
<!DOCTYPE html>
<html lang="en">
<head>
<meta charset="utf-8">
<title>Harborline Lending – Equity Loan Postcard</title>
<link href="https://fonts.googleapis.com/css2?family=Poppins:wght@500;700;800&family=Open+Sans:wght@400;600;700&display=swap" rel="stylesheet">
<style>
  :root{
    --red:#d21f2b;
    --red-dark:#b3141f;
    --navy:#16263d;
    --gold:#c8962e;
    --gold-light:#f0cf72;
    --ink:#1d1d1f;
    --grey:#4a4a4a;
    --paper:#ffffff;
    --page:#ffffff;
  }
  *{box-sizing:border-box;margin:0;padding:0}
  html,body{width:927px;height:1200px;overflow:hidden;background:var(--page)}
  body{position:relative;font-family:"Open Sans",Arial,sans-serif;color:var(--ink)}

  .postcard{position:absolute;left:124px;width:754px;height:473px;background:var(--paper);overflow:hidden;box-shadow:0 3px 10px rgba(0,0,0,.18)}
  .postcard--front{top:119px}
  .postcard--back{top:623px}

  .layer{position:absolute;inset:0;width:100%;height:100%}

  /* Front */
  .photo-house{position:absolute;left:300px;top:0;width:454px;height:391px;
    background:linear-gradient(180deg,#7d9cc9 0%,#a9bedc 30%,#5d6f8c 55%,#2f3a4e 80%,#4b4f55 100%)}
  .headline-band{position:absolute;left:0;top:0;width:754px;height:116px;
    background:linear-gradient(90deg,var(--red) 0%,var(--red) 62%,rgba(210,31,43,.55) 85%,rgba(210,31,43,0) 100%)}
  .headline{position:absolute;left:93px;top:34px;font-family:"Poppins",sans-serif;font-weight:800;font-size:37px;line-height:1;color:#fff;letter-spacing:.2px}
  .subhead{position:absolute;left:112px;top:80px;font-family:"Poppins",sans-serif;font-weight:500;font-size:19px;letter-spacing:2.2px;color:#fff}
  .benefits{position:absolute;left:93px;top:135px;list-style:none}
  .benefits li{font-size:16.5px;line-height:22.5px;color:var(--ink);display:flex;align-items:center;gap:8px}
  .benefits svg{width:11px;height:11px;flex:none}
  .brand{position:absolute;display:flex;align-items:center;gap:10px}
  .brand__mark{width:30px;height:30px;border-radius:50%;background:var(--gold)}
  .brand__name{font-family:"Open Sans",sans-serif;font-weight:600;color:var(--navy);line-height:1.05}
  .brand--front{left:40px;top:294px}
  .brand--front .brand__name{font-size:21px}
  .nmls{position:absolute;left:263px;top:279px;font-size:10.5px;color:var(--ink)}
  .call-bar{position:absolute;left:0;bottom:0;width:754px;height:82px;background:var(--navy)}
  .call-bar__label{position:absolute;left:120px;top:22px;width:104px;height:38px;background:var(--red);color:#fff;font-family:"Poppins",sans-serif;font-weight:500;font-size:21px;letter-spacing:3px;display:flex;align-items:center;justify-content:center}
  .call-bar__number{position:absolute;left:244px;top:13px;font-family:"Poppins",sans-serif;font-weight:800;font-size:41px;color:#fff;letter-spacing:.5px}

  /* Back */
  .brand--back{left:31px;top:40px}
  .brand--back .brand__name{font-size:19px}
  .back-copy{position:absolute;left:31px;top:112px;width:318px}
  .letter{font-size:14.5px;line-height:20.5px;color:var(--ink)}
  .letter__cta{margin-top:10px;font-size:13.5px;line-height:19px;font-weight:700;color:var(--ink)}
  .rule{margin-top:9px;width:311px;height:2px;background:var(--gold)}
  .disclaimer{margin-top:9px;font-size:8.4px;line-height:11.8px;color:var(--grey)}
  .back-call{position:absolute;left:31px;top:410px;display:flex;align-items:center;gap:14px}
  .back-call__label{width:66px;height:28px;background:var(--navy);color:#fff;font-family:"Poppins",sans-serif;font-weight:500;font-size:15px;letter-spacing:2px;display:flex;align-items:center;justify-content:center}
  .back-call__number{font-family:"Poppins",sans-serif;font-weight:700;font-size:29px;color:#fff}
  .stamp-box{position:absolute;left:560px;top:31px;width:78px;height:78px;border:1px solid #9a9a9a}
  .address-line{position:absolute;left:440px;width:216px;height:1px;background:#9a9a9a}
</style>
</head>
<body>

<section class="postcard postcard--front" aria-label="Postcard front">
  <div class="photo-house" role="img" aria-label="Photograph of a two-storey suburban house at dusk with a lit garage and porch"></div>
  <svg class="layer" viewBox="0 0 754 473" aria-hidden="true">
    <defs>
      <linearGradient id="goldFront" x1="0" y1="0" x2="1" y2="1">
        <stop offset="0" stop-color="#f0cf72"/>
        <stop offset=".5" stop-color="#c8962e"/>
        <stop offset="1" stop-color="#e8bd55"/>
      </linearGradient>
    </defs>
    <path d="M0,110 L560,110 C470,190 420,290 410,391 L0,391 Z" fill="#fff"/>
    <path d="M600,0 C500,120 420,240 395,391 L412,391 C440,250 520,130 640,0 Z" fill="url(#goldFront)"/>
    <rect x="0" y="383" width="754" height="8" fill="url(#goldFront)"/>
  </svg>
  <div class="headline-band"></div>
  <h1 class="headline">CASH OUT EQUITY LOAN</h1>
  <p class="subhead">ON YOUR INVESTMENT PROPERTY</p>
  <ul class="benefits">
    <li><svg viewBox="0 0 12 12"><path d="M1,6.5 L4.5,10 L11,2" fill="none" stroke="#d21f2b" stroke-width="1.8"/></svg>Loan based on your equity</li>
    <li><svg viewBox="0 0 12 12"><path d="M1,6.5 L4.5,10 L11,2" fill="none" stroke="#d21f2b" stroke-width="1.8"/></svg>Fast choice</li>
    <li><svg viewBox="0 0 12 12"><path d="M1,6.5 L4.5,10 L11,2" fill="none" stroke="#d21f2b" stroke-width="1.8"/></svg>No income qualifying</li>
    <li><svg viewBox="0 0 12 12"><path d="M1,6.5 L4.5,10 L11,2" fill="none" stroke="#d21f2b" stroke-width="1.8"/></svg>Competitive rates</li>
    <li><svg viewBox="0 0 12 12"><path d="M1,6.5 L4.5,10 L11,2" fill="none" stroke="#d21f2b" stroke-width="1.8"/></svg>Not based on credit scores</li>
  </ul>
  <p class="nmls">NMLS #481027</p>
  <div class="brand brand--front">
    <span class="brand__mark"></span>
    <span class="brand__name">Harborline<br>Lending, Inc.</span>
  </div>
  <div class="call-bar">
    <span class="call-bar__label">CALL</span>
    <span class="call-bar__number">800-555-0142</span>
  </div>
</section>

<section class="postcard postcard--back" aria-label="Postcard back">
  <svg class="layer" viewBox="0 0 754 473" aria-hidden="true">
    <defs>
      <linearGradient id="goldBack" x1="0" y1="0" x2="0" y2="1">
        <stop offset="0" stop-color="#f0cf72"/>
        <stop offset=".5" stop-color="#c8962e"/>
        <stop offset="1" stop-color="#e8bd55"/>
      </linearGradient>
    </defs>
    <path d="M0,379 L378,379 C370,415 356,445 342,473 L0,473 Z" fill="#d21f2b"/>
    <path d="M318,0 C405,150 405,330 335,473 L356,473 C428,330 428,150 342,0 Z" fill="url(#goldBack)"/>
  </svg>
  <div class="brand brand--back">
    <span class="brand__mark"></span>
    <span class="brand__name">Harborline<br>Lending, Inc.</span>
  </div>
  <div class="back-copy">
    <p class="letter">I am please to inform you that an equity bared loan is available for your investment property. This no qualifying loan is possible simply due to the equity you have.</p>
    <p class="letter__cta">Please call 800-555-0142 for a quote or email dana@harborline.loan</p>
    <div class="rule"></div>
    <p class="disclaimer">*Loan is subject to confirmation of equity and is for income property, investment property, rental property or business purpose, other restrictions and conditions apply. Please call for complete program requirements and details. Harborline Lending, Inc. 2250 Orchard Row, Suite 4, Fairmont CA 90000. Dana Whitfield, CA Dept of Real Estate – Real Estate Broker Lic. #00000000 NMLS #550190 CA Dept. of Real Estate Corporate Lic. #00000001, NMLS #481027.</p>
  </div>
  <div class="back-call">
    <span class="back-call__label">CALL</span>
    <span class="back-call__number">800-555-0142</span>
  </div>
  <div class="stamp-box"></div>
  <div class="address-line" style="top:293px"></div>
  <div class="address-line" style="top:324px"></div>
  <div class="address-line" style="top:353px"></div>
  <div class="address-line" style="top:383px"></div>
</section>

</body>
</html>
```